Diverse, up-scale salon needs eye-catching, unique business cards.

We are looking for a unique business card design for our stylist but that can also be multi functional and used for appointment reminder and referrals. I will need a design in a format that I can modify names and titles going forward. In the past we have had a dark background with the logo on one side, and stylist and contact information on the other but we are open to all ideas. I have included our mission statement as well as branded colors below. The statement doesn't need to go on the card, it's just a reference for target market. We need space for the stylists name, title, instagram handle and then the salons phone number, website and address. I am also open to adding a spot for a qr code linked to the stylist instagram or the salon booking link.

primary brand colors:
#333333 #233415 #36502a #93874a #000000
Mission statement:
Vessolin Hair Studio, a high-end salon located in the lively Downtown Farmington, Michigan, is committed to providing exceptional services in a welcoming and relaxed environment to meet the needs of our diverse clientele.
Our salon specializes in contemporary custom haircuts, coloring, extensions, and barbering and beard grooming services. Our team of skilled stylists is passionate and inventive in their hair styling techniques. At the heart of our salon are values centered on quality, innovation, creativity, and above all, comfort. These core values are evident in every appointment across our customizable array of services.
Our goal is to establish a benchmark for exceptional hair care for every human.
Website: www.vessolinhairstudio.example
instagram: @vessolinhairstudio
address: 41782 Pelham Crest Rd, Farmington MI
phone: 248-613-4087

Industry/Entity Type

Hair Salon

Contact Information for Business Card

Stylist name, title, phone, instagram, website, address, (optional qr code)

Requirements
Should not have
• Does not need mission statement on the card.

```html
<!DOCTYPE html>
<html lang="en">
<head>
<meta charset="utf-8">
<title>Vessolin Hair Studio – Stylist Business Card</title>
<link rel="stylesheet" href="https://fonts.googleapis.com/css2?family=Montserrat:wght@400;600&family=Open+Sans:wght@400&display=swap">
<style>
  :root {
    --backdrop: #2b2d30;
    --card: #1c1c1c;
    --gold: #93874a;
    --text-light: #e6e6e6;
  }
  * { margin: 0; padding: 0; box-sizing: border-box; }
  html, body { width: 1200px; height: 952px; overflow: hidden; }
  body {
    background: var(--backdrop);
    font-family: "Open Sans", sans-serif;
    position: relative;
  }
  .card {
    position: absolute;
    top: 316px;
    width: 520px;
    height: 320px;
    background: var(--card);
    border-radius: 22px;
    overflow: hidden;
  }
  .card--front { left: 60px; }
  .card--back { left: 620px; }

  /* front */
  .edge-band {
    position: absolute;
    left: 0; top: 0;
    width: 28px; height: 100%;
    background: var(--gold);
  }
  .name-tab {
    position: absolute;
    left: 0; top: 26px;
    width: 64px; height: 44px;
    background: var(--gold);
    border-radius: 0 14px 14px 0;
    display: flex; align-items: center; justify-content: center;
    padding-left: 10px;
  }
  .stylist {
    position: absolute;
    left: 80px; top: 28px;
  }
  .stylist__name {
    font-family: "Montserrat", sans-serif;
    font-size: 25px;
    line-height: 1;
    color: var(--gold);
    text-transform: uppercase;
    letter-spacing: 0.5px;
    white-space: nowrap;
  }
  .stylist__name .first { font-weight: 400; }
  .stylist__name .last { font-weight: 600; }
  .stylist__title {
    font-size: 11px;
    color: var(--text-light);
    margin-top: 5px;
  }
  .contact-list {
    position: absolute;
    left: 46px; top: 104px;
    list-style: none;
  }
  .contact-row {
    display: flex;
    align-items: center;
    margin-bottom: 14px;
  }
  .contact-row svg { width: 18px; height: 18px; flex: none; }
  .contact-row .divider {
    width: 1px; height: 24px;
    background: var(--text-light);
    margin: 0 12px 0 10px;
    transform: skewX(-20deg);
  }
  .contact-row p {
    font-size: 11px;
    line-height: 1.4;
    color: var(--text-light);
    white-space: nowrap;
  }
  .brand-mark {
    position: absolute;
    right: 32px; bottom: 36px;
    display: flex; align-items: center; gap: 10px;
    white-space: nowrap;
  }
  .brand-mark__ring {
    width: 40px; height: 40px;
    flex: none;
    border: 2px solid var(--gold);
    border-radius: 50%;
  }
  .brand-mark__name {
    font-family: "Montserrat", sans-serif;
    font-weight: 600;
    font-size: 15px;
    letter-spacing: 2px;
    text-transform: uppercase;
    color: var(--gold);
  }

  /* back */
  .back-tab {
    position: absolute;
    width: 26px; height: 92px;
    background: var(--gold);
  }
  .back-tab--top { left: 0; top: 34px; border-radius: 0 8px 8px 0; }
  .back-tab--bottom { right: 0; bottom: 34px; border-radius: 8px 0 0 8px; }
  .card--back .brand-mark {
    right: auto; bottom: auto;
    left: 50%; top: 50%;
    transform: translate(-50%, -50%);
  }
</style>
</head>
<body>

<section class="card card--front" aria-label="Stylist card, front">
  <div class="edge-band"></div>
  <div class="name-tab">
    <svg width="18" height="18" viewBox="0 0 24 24" aria-hidden="true">
      <circle cx="12" cy="8" r="5" fill="#fff"/>
      <path d="M3 22c0-5 4-8 9-8s9 3 9 8z" fill="#fff"/>
    </svg>
  </div>
  <div class="stylist">
    <h1 class="stylist__name"><span class="first">Nora</span> <span class="last">Castellan</span></h1>
    <p class="stylist__title">Senior Stylist</p>
  </div>

  <ul class="contact-list">
    <li class="contact-row">
      <svg viewBox="0 0 24 24" aria-hidden="true"><path d="M6.6 10.8a15.1 15.1 0 0 0 6.6 6.6l2.2-2.2c.3-.3.7-.4 1-.2 1.1.4 2.3.6 3.6.6.6 0 1 .4 1 1V20c0 .6-.4 1-1 1A17 17 0 0 1 3 4c0-.6.4-1 1-1h3.5c.6 0 1 .4 1 1 0 1.3.2 2.5.6 3.6.1.3 0 .7-.2 1z" fill="#93874a"/></svg>
      <span class="divider"></span>
      <p>248-613-4087<br>@noracastellan.hair</p>
    </li>
    <li class="contact-row">
      <svg viewBox="0 0 24 24" aria-hidden="true"><path d="M12 2l7 20-7-5-7 5z" fill="#93874a"/></svg>
      <span class="divider"></span>
      <p>www.vessolinhairstudio.example<br>nora@vessolinhairstudio.example</p>
    </li>
    <li class="contact-row">
      <svg viewBox="0 0 24 24" aria-hidden="true"><path d="M12 3l10 9h-3v9h-5v-6h-4v6H5v-9H2z" fill="#93874a"/></svg>
      <span class="divider"></span>
      <p>41782 Pelham Crest Rd,<br>Farmington MI</p>
    </li>
  </ul>

  <div class="brand-mark">
    <span class="brand-mark__ring"></span>
    <span class="brand-mark__name">Vessolin Hair Studio</span>
  </div>
</section>

<section class="card card--back" aria-label="Stylist card, back">
  <div class="back-tab back-tab--top"></div>
  <div class="back-tab back-tab--bottom"></div>
  <div class="brand-mark">
    <span class="brand-mark__ring"></span>
    <span class="brand-mark__name">Vessolin Hair Studio</span>
  </div>
</section>

</body>
</html>
```